Business Card Design

Just looking for a good designs that looks good with our company logo. I'd like it to be simple and to the point. Just including contact information, our logo, and my name somewhere on the card so future clients know who they're contacting, and a couple services offered. The two images I attached are pictures of our logo. I don't care which color they they are, I just attached both images to give a reference of logo colors depending on the color of the card.
Names: Carl Whitby
Phone: 816-555-0147
Email: greenstripeyard@fernmail.test
Services offered:
Mowing
Fertilization
Aeration
Bed & tree maintenance
and more.
Business
Names: Carl Whitby
Phone: 816-555-0147
(no website)

```html
<!DOCTYPE html>
<html lang="en">
<head>
<meta charset="utf-8">
<title>Fairway Turf – Business Card</title>
<link rel="stylesheet" href="https://fonts.googleapis.com/css2?family=Lora:ital,wght@0,400;0,700;1,400;1,600&family=Roboto+Condensed:wght@700&display=swap">
<style>
  :root {
    --backdrop: #e6e6e6;
    --card: #efefec;
    --ink: #2f3140;
    --navy: #0f2a5c;
    --salmon: #ec6a52;
    --salmon-fade: #fbe3dc;
    --brand-red: #e0463a;
    --service-green: #2f9d3a;
    --service-red: #e0513b;
    --badge-green: #2e9a2f;
    --badge-dark: #4a1a1a;
    --hill-dark: #2f8a2a;
    --hill-light: #7cc23a;
  }
  * { box-sizing: border-box; margin: 0; padding: 0; }
  html, body { width: 1200px; height: 960px; overflow: hidden; }
  body {
    background: radial-gradient(ellipse at center, #f4f4f4 0%, var(--backdrop) 70%, #d6d6d6 100%);
    font-family: "Lora", Georgia, serif;
    position: relative;
  }
  .card {
    position: absolute;
    left: 100px; top: 190px;
    width: 1000px; height: 580px;
    background: var(--card);
    overflow: hidden;
    box-shadow: 0 10px 30px rgba(0,0,0,.18);
  }
  .contact-list { list-style: none; }
  .contact {
    position: absolute; right: 0;
    display: flex; align-items: center; justify-content: flex-end;
    padding-right: 22px;
    background: linear-gradient(90deg, var(--salmon) 0%, #f49a85 55%, var(--salmon-fade) 100%);
    color: var(--ink);
    border-radius: 4px 0 0 4px;
    white-space: nowrap;
  }
  .contact::after {
    content: ""; flex: 0 0 13px; width: 13px; height: 13px; background: var(--navy); margin-left: 10px;
  }
  .contact--name { top: 28px; width: 420px; height: 58px; font-size: 30px; padding-right: 40px; }
  .contact--phone { top: 110px; width: 330px; height: 48px; font-size: 30px; }
  .contact--email { top: 172px; width: 360px; height: 46px; font-size: 17px; font-weight: 700; }
  .contact .icon { flex: 0 0 20px; width: 20px; height: 20px; margin-right: 6px; }
  .quality-badge {
    position: absolute;
    left: 150px; top: 195px;
    display: flex; align-items: center;
    font-family: "Roboto Condensed", Arial, sans-serif;
    font-weight: 700;
  }
  .quality-badge .percent {
    color: var(--badge-green);
    font-size: 34px; line-height: 1;
    display: flex; flex-direction: column; align-items: center;
  }
  .quality-badge .percent small { font-size: 10px; letter-spacing: 1px; }
  .quality-badge .guarantee {
    margin-left: 6px;
    padding: 4px 18px 4px 30px;
    background: linear-gradient(90deg, var(--brand-red), var(--badge-dark));
    color: #fff6c8;
    font-size: 20px;
  }
  .brand {
    position: absolute;
    left: 270px; top: 250px;
    width: 400px;
    display: flex; align-items: center; justify-content: center; gap: 14px;
  }
  .brand .mark {
    flex: 0 0 26px; width: 26px; height: 26px; border-radius: 50%;
    background: var(--brand-red);
  }
  .brand .name {
    font-weight: 700;
    font-size: 46px;
    color: var(--ink);
    white-space: nowrap;
  }
  .services {
    position: absolute;
    left: 190px; top: 330px; width: 560px;
    text-align: center;
    font-style: italic;
    font-size: 28px;
    line-height: 36px;
  }
  .services .green { color: var(--service-green); }
  .services .red { color: var(--service-red); }
  .landscape-art {
    position: absolute;
    left: 0; bottom: 0; width: 1000px; height: 130px;
    background: linear-gradient(180deg, var(--hill-light) 0%, var(--hill-dark) 100%);
    border-radius: 0 70% 0 0 / 0 60% 0 0;
  }
</style>
</head>
<body>
  <section class="card" aria-label="Fairway Turf business card">
    <ul class="contact-list">
      <li class="contact contact--name">Carl Whitby</li>
      <li class="contact contact--phone">
        <svg class="icon" viewBox="0 0 24 24" aria-hidden="true"><path fill="#0f2a5c" d="M6.6 10.8a15 15 0 0 0 6.6 6.6l2.2-2.2c.3-.3.7-.4 1-.2 1.1.4 2.3.6 3.6.6.6 0 1 .4 1 1V20c0 .6-.4 1-1 1A17 17 0 0 1 3 4c0-.6.4-1 1-1h3.5c.6 0 1 .4 1 1 0 1.3.2 2.5.6 3.6.1.3 0 .7-.2 1z"/></svg>
        816-555-0147
      </li>
      <li class="contact contact--email">greenstripeyard@fernmail.test</li>
    </ul>

    <div class="quality-badge">
      <span class="percent">100%<small>QUALITY</small></span>
      <span class="guarantee">Guaranteed</span>
    </div>

    <div class="brand">
      <span class="mark" aria-hidden="true"></span>
      <span class="name">Fairway Turf</span>
    </div>

    <p class="services">
      <span class="green">Mowing .Fertilization .Aeration</span><br>
      <span class="red">Bed and tree maintenance</span><br>
      <span class="green">and more ...</span>
    </p>

    <div class="landscape-art" role="img" aria-label="Illustration of rolling green hills with small trees and a winding path"></div>
  </section>
</body>
</html>
```